Animal Eye Clinic needs a Business card

We are a new veterinary ophthalmology practice (Ridgeline Pet Vision Care) and we need a business card designed. We only see animal eyes - we are not a regular veterinary clinic. We already have a logo. We are looking for a professional, good looking business card to hand out to our clients. We are looking for something simple but professional and contemporary. Our logo is likely the only picture/graphic that needs to be on the card.
Updates

Contact Information for Business Card

Delia Vossman, BSc, DVM, MSc, DipACVO
Veterinary Ophthalmologist

Phone: 250.418.3927
Email: ridgelinepetvisioncare@mailbox-example.net
Website: ridgelinepetvisioncare-example.net
Address: 1874 Thornbury Rd
Kelowna, BC, V1X 4M9

Colors

Designer to choose colors to be used in the design.

Requirements
Must have
• Our logo (attached)

```html
<!DOCTYPE html>
<html lang="en">
<head>
<meta charset="utf-8">
<title>Ridgeline Pet Vision Care – Business Card</title>
<link href="https://fonts.googleapis.com/css2?family=Arimo:wght@400;700&family=Roboto+Condensed:wght@700&display=swap" rel="stylesheet">
<style>
  :root {
    --teal: #1a9aab;
    --ink: #555a5e;
    --paper: #ffffff;
    --slate: #767676;
    --slate-light: #ececec;
    --backdrop: #d9d9d9;
  }
  html, body {
    margin: 0;
    padding: 0;
    overflow: hidden;
  }
  body {
    width: 1200px;
    height: 800px;
    background: var(--backdrop);
    position: relative;
    font-family: "Arimo", Arial, sans-serif;
  }
  .card {
    position: absolute;
    top: 240px;
    width: 560px;
    height: 320px;
    box-sizing: border-box;
    overflow: hidden;
    box-shadow: 0 6px 18px rgba(0,0,0,0.18);
  }

  /* Front */
  .card-front {
    left: 30px;
    background: var(--paper);
    border-bottom: 9px solid var(--teal);
  }
  .brand {
    position: absolute;
    left: 36px;
    top: 58px;
    display: flex;
    align-items: center;
    gap: 12px;
  }
  .brand-dot {
    width: 34px;
    height: 34px;
    border-radius: 50%;
    background: var(--teal);
    flex: none;
  }
  .brand-name {
    margin: 0;
    font-family: "Arimo", Arial, sans-serif;
    font-weight: 700;
    font-size: 17px;
    line-height: 1.15;
    letter-spacing: 0.5px;
    text-transform: uppercase;
    color: var(--teal);
    width: 180px;
  }
  .person {
    position: absolute;
    left: 36px;
    bottom: 46px;
  }
  .person-name {
    margin: 0;
    font-family: "Roboto Condensed", "Arial Narrow", sans-serif;
    font-weight: 700;
    font-size: 15px;
    text-transform: uppercase;
    color: var(--teal);
    letter-spacing: 0.2px;
  }
  .person-title {
    margin: 3px 0 0;
    font-size: 13px;
    color: var(--ink);
  }
  .contact {
    position: absolute;
    left: 262px;
    top: 128px;
    font-size: 12px;
    line-height: 1.45;
    color: var(--ink);
    list-style: none;
    margin: 0;
    padding: 0;
  }
  .contact-address {
    margin-bottom: 6px;
  }
  .contact-line {
    display: flex;
    align-items: center;
    gap: 7px;
  }
  .contact-icon {
    width: 11px;
    height: 11px;
    flex: none;
    fill: var(--teal);
  }

  /* Back */
  .card-back {
    left: 610px;
    background: var(--slate);
  }
  .emblem-area {
    position: absolute;
    left: 40px;
    top: 60px;
    width: 230px;
    height: 230px;
    border-radius: 50%;
    background: var(--slate-light);
  }
  .back-text {
    position: absolute;
    right: 36px;
    top: 118px;
    text-align: right;
    color: var(--paper);
  }
  .back-name {
    margin: 0;
    font-weight: 700;
    font-size: 21px;
    line-height: 1.15;
    text-transform: uppercase;
    letter-spacing: 0.5px;
    width: 220px;
    margin-left: auto;
  }
  .back-web {
    margin: 10px 0 0;
    font-size: 9.5px;
    letter-spacing: 0.6px;
    text-transform: uppercase;
  }
</style>
</head>
<body>

  <section class="card card-front">
    <div class="brand">
      <span class="brand-dot"></span>
      <h1 class="brand-name">Ridgeline Pet Vision Care</h1>
    </div>

    <div class="person">
      <p class="person-name">Delia Vossman, BSc, DVM, MSc, DipACVO</p>
      <p class="person-title">Veterinary Ophthalmologist</p>
    </div>

    <ul class="contact">
      <li class="contact-address">1874 Thornbury Rd<br>Kelowna, BC, V1X 4M9</li>
      <li class="contact-line">
        <svg class="contact-icon" viewBox="0 0 24 24" aria-hidden="true"><path d="M6.6 10.8a15.5 15.5 0 0 0 6.6 6.6l2.2-2.2a1 1 0 0 1 1-.25 11.4 11.4 0 0 0 3.6.57 1 1 0 0 1 1 1V20a1 1 0 0 1-1 1A17 17 0 0 1 3 4a1 1 0 0 1 1-1h3.5a1 1 0 0 1 1 1c0 1.25.2 2.45.57 3.57a1 1 0 0 1-.25 1z"/></svg>
        250.418.3927
      </li>
      <li class="contact-line">
        <svg class="contact-icon" viewBox="0 0 24 24" aria-hidden="true"><path d="M2 5h20v14H2z M2 5l10 8 10-8" fill="none" stroke="currentColor"/><path d="M2 5h20v14H2zm2 2v.4l8 6.4 8-6.4V7z" fill-rule="evenodd"/></svg>
        ridgelinepetvisioncare@mailbox-example.net
      </li>
      <li class="contact-line">
        <svg class="contact-icon" viewBox="0 0 24 24" aria-hidden="true"><path d="M12 2a10 10 0 1 0 0 20 10 10 0 0 0 0-20zm0 2c.9 0 2.2 2 2.7 5H9.3C9.8 6 11.1 4 12 4zM4.3 13a8 8 0 0 1 0-2h3a17 17 0 0 0 0 2zm.6 2h2.6a11 11 0 0 0 1.4 3.8A8 8 0 0 1 4.9 15zm2.6-6H4.9a8 8 0 0 1 4-3.8A11 11 0 0 0 7.5 9zm4.5 11c-.9 0-2.2-2-2.7-5h5.4c-.5 3-1.8 5-2.7 5zm2.9-7H9.1a15 15 0 0 1 0-2h5.8a15 15 0 0 1 0 2zm.2 5.8a11 11 0 0 0 1.4-3.8h2.6a8 8 0 0 1-4 3.8zM16.7 13a17 17 0 0 0 0-2h3a8 8 0 0 1 0 2zm-.2-4a11 11 0 0 0-1.4-3.8 8 8 0 0 1 4 3.8z"/></svg>
        ridgelinepetvisioncare-example.net
      </li>
    </ul>
  </section>

  <section class="card card-back">
    <div class="emblem-area" role="img" aria-label="Large emblem area of the practice mark on a light circle"></div>
    <div class="back-text">
      <h2 class="back-name">Ridgeline Pet Vision Care</h2>
      <p class="back-web">www.ridgelinepetvisioncare-example.net</p>
    </div>
  </section>

</body>
</html>
```